Tiny Meadow Product Label for Tear-Free Head-to-Toe Wash

Need a bottle label design for a new line of natural products targeting infants and children. Products are Pediatrician-developed and paraben-free, sulfate-free, fragrance-free, and cruelty-free. Design should be clean and have a high-end feel to it. Will need other product labels in Tiny Meadow line designed as well in upcoming projects.

Target Market(s)

Newborn to young elementary age children and their parents

Industry/Entity Type

Cosmetics/Beauty

Font styles to use
Other font styles liked:
• Brand fonts are Jost and Sonorous

Colors

Designer to choose colors to be used in the design.

Requirements
Must have
• Tiny Meadow logo, Pediatrician Developed logo, and a clean high-end feel to it. The label must fit the specialty bottle we will be using (label measurements and diagram will be provided) for the front and back of bottle only (NOT the side labels). It must include our list of ingredients (will provide once designer selected).
Nice to have
• Should stand out on the shelf of other baby products due to it's clean simplicity and high-end feel
Should not have
• too much of a "kiddie" feel to it (targeting the parents not the kids)

```html
<!DOCTYPE html>
<html lang="en">
<head>
<meta charset="utf-8">
<title>Tiny Meadow – Tear-Free Head-to-Toe Wash Label</title>
<link rel="stylesheet" href="https://fonts.googleapis.com/css2?family=Jost:ital,wght@0,400;0,500;0,600;1,700&family=Nunito:wght@900&display=swap">
<style>
  :root {
    --bronze: #99722f;
    --paper: #ffffff;
    --ink: #2b2622;
    --stage: #eceae6;
  }
  * { box-sizing: border-box; margin: 0; padding: 0; }
  html, body { width: 1200px; height: 1200px; overflow: hidden; }
  body {
    background: var(--stage);
    font-family: "Jost", sans-serif;
    position: relative;
  }
  .label {
    position: absolute;
    top: 205px;
    width: 540px;
    height: 780px;
    border-radius: 90px 90px 0 0;
    overflow: hidden;
    background: var(--bronze);
    box-shadow: 0 6px 24px rgba(0,0,0,0.08);
  }
  .label--front { left: 40px; }
  .label--back { left: 620px; }
  .label__top {
    position: absolute; left: 0; top: 0;
    width: 100%; height: 306px;
    background: var(--paper);
  }

  /* Brand lockup */
  .brand {
    position: absolute; left: 42px; top: 158px;
    display: flex; align-items: center; gap: 36px;
  }
  .brand__dot {
    width: 84px; height: 84px; border-radius: 50%;
    border: 3px solid var(--bronze);
    flex: none;
  }
  .brand__name {
    font-weight: 600; font-size: 37px; color: var(--ink);
    letter-spacing: 1px; line-height: 1;
  }
  .brand__tagline {
    margin-top: 12px; margin-left: 6px;
    font-weight: 600; font-size: 10px; letter-spacing: 2px;
    color: var(--bronze); text-transform: uppercase;
  }

  .product-title {
    position: absolute; left: 32px; top: 346px; width: 490px;
    font-family: "Nunito", sans-serif; font-weight: 900;
    font-size: 46px; line-height: 1.1; color: var(--paper);
    white-space: nowrap;
  }
  .product-claim {
    position: absolute; left: 0; top: 469px;
    width: 453px; height: 46px;
    background: var(--paper);
    border-radius: 0 23px 23px 0;
    padding-left: 32px;
    display: flex; align-items: center;
    font-size: 22px; color: var(--ink);
  }
  .free-badges {
    position: absolute; left: 30px; top: 553px;
    display: flex; gap: 20px;
  }
  .free-badge {
    width: 86px; height: 86px; border-radius: 50%;
    border: 2px dotted var(--paper);
    display: flex; flex-direction: column; align-items: center; justify-content: center;
    color: var(--paper); font-weight: 600; font-size: 9.5px; letter-spacing: 1px;
    text-align: center; line-height: 1.6;
  }
  .net-weight {
    position: absolute; left: 32px; top: 708px;
    font-size: 25px; font-weight: 500; color: var(--ink);
  }

  /* Back panel */
  .back-intro {
    position: absolute; left: 73px; right: 73px; top: 126px;
    font-size: 20px; line-height: 1.38; color: var(--bronze);
    text-align: justify;
  }
  .back-body {
    position: absolute; left: 73px; right: 73px; top: 320px;
    color: var(--paper); font-size: 20px; line-height: 1.36;
  }
  .back-body h2 {
    font-style: italic; font-weight: 700; font-size: 26px;
    color: var(--ink); line-height: 1.2;
  }
  .back-body p { text-align: justify; }
  .back-body .section + .section { margin-top: 10px; }
  .maker { margin-top: 14px; }
  .maker__lead { font-style: italic; font-weight: 700; color: var(--ink); }
  .pediatric-badge {
    position: absolute; left: 377px; top: 638px;
    width: 96px; height: 96px; border-radius: 50%;
    border: 2px solid var(--ink);
  }
</style>
</head>
<body>

  <section class="label label--front">
    <div class="label__top"></div>
    <div class="brand">
      <div class="brand__dot"></div>
      <div>
        <div class="brand__name">Tiny Meadow</div>
        <div class="brand__tagline">Gentle care from day one</div>
      </div>
    </div>
    <h1 class="product-title">Tear-Free Head-<br>to-Toe Wash</h1>
    <div class="product-claim">Naturally formulated for delicate skin</div>
    <div class="free-badges">
      <div class="free-badge">PARABEN<br>FREE</div>
      <div class="free-badge">SULFATE<br>FREE</div>
      <div class="free-badge">FRAGRANCE<br>FREE</div>
      <div class="free-badge">CRUELTY<br>FREE</div>
    </div>
    <div class="net-weight">Net wt: 73 mL/2,43 fl.oz</div>
  </section>

  <section class="label label--back">
    <div class="label__top"></div>
    <p class="back-intro">A gentle, all-in-one cleanser made with natural ingredients to protect and nourish baby’s delicate hair and skin. Pediatrician-developed and suitable for daily use from newborn onwards.</p>
    <div class="back-body">
      <div class="section">
        <h2>Directions:</h2>
        <p>Dispense a small amount into hands or washcloth. Gently massage into wet hair and skin. Rinse thoroughly. Avoid contact with eyes.</p>
      </div>
      <div class="section">
        <h2>Ingredients:</h2>
        <p>Aqua, Glycerin, Decyl Glucoside, Sodium Lauroyl Lactylate, Coco-Glucoside, Glyceryl Oleate, Xanthan Gum, Sodium Benzoate, Citric Acid.<br>(Full list to be finalized.)</p>
      </div>
      <div class="maker">
        <div class="maker__lead">Manufactured for</div>
        <div>Tiny Meadow Co.</div>
        <div>tinymeadow.com/Made in USA</div>
      </div>
    </div>
    <div class="pediatric-badge"></div>
  </section>

</body>
</html>
```